Marlowe Group needs a business card

I would like the card to be simple but modern and elegant.
I like black and white.
or black and gold.
we are a private finance lender and also are involved in property and property developments.

please look at the business card photos i provided i would like M.G only one one side and all the other details on the other side use fonts that tie in with my theme.

Industry/Entity Type

Finance

Contact Information for Business Card

Marlowe Group (M.G) Daniel Marlowe M: 0413586207 E: danmarl@inboxmail.test

Font styles to use
Other font styles liked:
• Use fonts that would reflect our business

Colors
000000
ffffff

Requirements
Must have
• one side of details
• other side has either M.G or Marlowe Group like in the photos provided

```html
<!DOCTYPE html>
<html lang="en">
<head>
<meta charset="UTF-8">
<title>Marlowe Group – Business Card</title>
<link href="https://fonts.googleapis.com/css2?family=Lato:wght@400;700&display=swap" rel="stylesheet">
<style>
  :root {
    --backdrop: #57564b;
    --card: #3b3034;
    --card-edge: #2c2427;
    --gold: #dcc07a;
  }
  html, body {
    margin: 0;
    padding: 0;
    width: 1200px;
    height: 900px;
    overflow: hidden;
    background: var(--backdrop);
  }
  .canvas {
    position: relative;
    width: 1200px;
    height: 900px;
    display: flex;
    flex-direction: column;
    align-items: center;
    justify-content: center;
    gap: 60px;
  }
  .card {
    position: relative;
    width: 560px;
    height: 320px;
    background: var(--card);
    border-radius: 3px;
    box-shadow: 0 2px 0 var(--card-edge), 0 12px 30px rgba(0,0,0,0.35);
    font-family: "Lato", Arial, sans-serif;
    color: var(--gold);
  }
  .card-front .brand-name {
    position: absolute;
    right: 48px;
    bottom: 64px;
    margin: 0;
    font-size: 28px;
    font-weight: 400;
    letter-spacing: 0.5px;
  }
  .card-back .contact {
    position: absolute;
    right: 48px;
    bottom: 48px;
    margin: 0;
    padding: 0;
    list-style: none;
    text-align: right;
    font-size: 16px;
    line-height: 1.5;
    letter-spacing: 0.6px;
  }
  .card-back .person-name {
    font-weight: 700;
    text-transform: uppercase;
    font-size: 17px;
    letter-spacing: 1px;
  }
  .card-back .divider {
    display: inline-block;
    width: 18px;
    height: 2px;
    background: var(--gold);
    vertical-align: middle;
  }
</style>
</head>
<body>
  <main class="canvas">
    <section class="card card-front" aria-label="Card front">
      <h1 class="brand-name">Marlowe Group</h1>
    </section>
    <section class="card card-back" aria-label="Card back">
      <ul class="contact">
        <li class="person-name">Daniel Marlowe</li>
        <li><span class="divider"></span></li>
        <li>M: 0413586207</li>
        <li><span class="divider"></span></li>
        <li>E: danmarl@inboxmail.test</li>
      </ul>
    </section>
  </main>
</body>
</html>
```